Business card design for holistic health care clinic

We need a double-sided business card design for our holistic health care clinic that integrates our logo design and also its color scheme. My business is called Valmira. It is an integrative medicine clinic. You have already done the logo for me. Please ensure an elegant and upscale design that is not cluttered, but still has all the necessary information (please see below for details).

Target Market(s)

Wellness, fitness, rehabilitation for educated, well-traveled open-minded clients who are focused on natural, organic, balanced and preventive healthcare and lifestyle.

Industry/Entity Type

Medical

Contact Information for Business Card

Modern, clean.

Number of Pages Required

1 page

Font styles to use
Serif
Sans Serif

Colors

Designer to choose colors to be used in the design.

Requirements
Must have
• Logo on one side, all other information on the other side.
• Other information should include:
• Tobias Wrenfeld - DOE, CPT, LMT
• 4100 East Marrow Drive
• Austin, TX 78119
• 512 555 0148
• 818 555 0192
• info@ValmiraHealth.example
• t.wrenfeld@ValmiraHealth.example
Nice to have
• Darker background on front - but not totally black - shaded/dark gray.

```html
<!DOCTYPE html>
<html lang="en">
<head>
<meta charset="utf-8">
<title>Valmira – Business Card</title>
<link rel="stylesheet" href="https://fonts.googleapis.com/css2?family=Roboto:ital,wght@0,400;0,500;0,700;1,500&family=Roboto+Condensed:wght@500;700&display=swap">
<style>
  :root {
    --page-bg: #e4e4e4;
    --card-dark: #2a2a2a;
    --card-light: #f2f2f2;
    --brand-blue: #0f8fcf;
    --soft-blue: #c6e1ef;
    --band-grey: #b3b3b3;
    --text-light: #f4f4f4;
    --text-grey: #5e5e5e;
  }
  * { margin: 0; padding: 0; box-sizing: border-box; }
  html, body { width: 1200px; height: 960px; overflow: hidden; }
  body {
    background: var(--page-bg);
    font-family: "Roboto", Arial, sans-serif;
    position: relative;
  }
  .card {
    position: absolute;
    width: 600px;
    height: 343px;
    overflow: hidden;
  }
  .card--front { left: 314px; top: 113px; background: var(--card-dark); }
  .card--back  { left: 311px; top: 472px; background: var(--card-light); }

  .brand-name {
    position: absolute;
    font-family: "Roboto", Arial, sans-serif;
    font-weight: 700;
    color: var(--brand-blue);
    line-height: 1;
    letter-spacing: 0.5px;
    text-transform: uppercase;
  }
  .brand-descriptor {
    position: absolute;
    font-weight: 500;
    color: var(--brand-blue);
    white-space: nowrap;
  }

  .card--front .brand-name { left: 58px; top: 78px; font-size: 48px; }
  .card--front .brand-descriptor { left: 62px; top: 125px; font-size: 15.5px; }

  .address {
    position: absolute;
    left: 64px; top: 181px;
    font-size: 15px;
    font-style: normal;
    line-height: 19px;
    color: var(--text-light);
  }
  .contact-list {
    position: absolute;
    left: 64px; top: 228px;
    list-style: none;
    font-size: 15px;
    color: var(--text-light);
  }
  .contact-list li {
    display: flex;
    align-items: center;
    height: 19.5px;
  }
  .contact-list svg { width: 16px; height: 14px; margin-right: 7px; fill: var(--brand-blue); }

  .holder {
    position: absolute;
    right: 22px; top: 262px;
    font-family: "Roboto Condensed", Arial, sans-serif;
    color: var(--brand-blue);
    white-space: nowrap;
    text-align: right;
  }
  .holder__name { font-size: 19px; font-weight: 700; text-transform: uppercase; }
  .holder__credentials { font-size: 12.5px; font-weight: 700; margin-left: 3px; }

  .footer-band {
    position: absolute;
    left: 0; bottom: 0;
    width: 600px; height: 26px;
    background: linear-gradient(to right, var(--brand-blue) 0 392px, var(--band-grey) 392px);
  }
  .footer-band__web {
    position: absolute;
    left: 64px; top: 4px;
    font-size: 14.5px;
    letter-spacing: 2.2px;
    color: var(--text-light);
  }
  .footer-band__dot {
    position: absolute;
    left: 378px; top: -4px;
    width: 28px; height: 28px;
    border-radius: 50%;
    background: var(--text-light);
  }

  .card--back .decor-circle {
    position: absolute;
    left: 380px; top: 40px;
    width: 300px; height: 300px;
    border-radius: 50%;
    background: var(--soft-blue);
  }
  .card--back .brand-name { left: 72px; top: 227px; font-size: 40px; }
  .card--back .brand-descriptor { left: 75px; top: 264px; font-size: 13px; }
  .tagline {
    position: absolute;
    left: 72px; top: 284px;
    font-size: 16px;
    font-style: italic;
    font-weight: 500;
    color: var(--text-grey);
  }
</style>
</head>
<body>

<section class="card card--front" aria-label="Business card front">
  <div class="brand-name">Valmira</div>
  <div class="brand-descriptor">Integrative Holistic Medicine</div>

  <address class="address">
    4100 East Marrow Drive<br>
    Austin, TX 78119
  </address>

  <ul class="contact-list">
    <li>
      <svg viewBox="0 0 16 14" aria-hidden="true"><path d="M3 1c1-.6 1.6 0 2.2 1.2l.8 1.7c.3.7 0 1.2-.6 1.6l-.7.4c.6 1.6 1.9 2.9 3.4 3.6l.5-.7c.4-.6 1-.8 1.6-.5l1.7.9c1.1.6 1.5 1.3.8 2.2-.9 1.2-2.2 1.6-3.7 1C5.8 11.3 3.4 8.9 2.3 5.6 1.8 3.9 2 2 3 1z"/></svg>
      512 555 0148
    </li>
    <li>
      <svg viewBox="0 0 16 14" aria-hidden="true"><path d="M4.5 0h6c.8 0 1.3.5 1.3 1.3v11.4c0 .8-.5 1.3-1.3 1.3h-6c-.8 0-1.3-.5-1.3-1.3V1.3C3.2.5 3.7 0 4.5 0zm.4 1.6v9.6h5.2V1.6zM7.5 11.8a.8.8 0 100 1.6.8.8 0 000-1.6z"/></svg>
      818 555 0192
    </li>
    <li>
      <svg viewBox="0 0 16 14" aria-hidden="true"><path d="M1.5 3h13v.6L8 8 1.5 3.6zM1.5 5.2 8 9.6l6.5-4.4V12h-13z"/></svg>
      t.wrenfeld@ValmiraHealth.example
    </li>
  </ul>

  <div class="holder">
    <span class="holder__name">Tobias Wrenfeld</span><span class="holder__credentials">- DOE, CPT, LMT</span>
  </div>

  <div class="footer-band">
    <span class="footer-band__web">www.ValmiraHealth.example</span>
    <span class="footer-band__dot" aria-hidden="true"></span>
  </div>
</section>

<section class="card card--back" aria-label="Business card back">
  <div class="decor-circle" aria-hidden="true"></div>
  <div class="brand-name">Valmira</div>
  <div class="brand-descriptor">Integrative Holistic Medicine</div>
  <p class="tagline">helping the body help itself</p>
</section>

</body>
</html>
```